Corvane Capital Business Cards

These are professional business cards that are for my family office.
Put fake emails and phone numbers as of now until I finalize those components. This family office controls my families investments, assets, and future. The cards should be professional.
..
.
.
.
I just uploaded another variation of a logo I would like to see as a business card to I am inbeteen which logo to use

Target Market(s)

business

Industry/Entity Type

business

Contact Information for Business Card

Professional, wealth related, finance related.

Requirements
Must have
• Logo

```html
<!DOCTYPE html>
<html lang="en">
<head>
<meta charset="utf-8">
<title>Corvane Capital Business Cards</title>
<link href="https://fonts.googleapis.com/css2?family=Cinzel:wght@500;600&family=Arimo:wght@400&display=swap" rel="stylesheet">
<style>
  :root {
    --backdrop: #3b3b3d;
    --navy: #1b1f2c;
    --white: #ffffff;
    --muted: #c9ccd4;
    --dot-grey: #a9a9a9;
  }
  * { margin: 0; padding: 0; box-sizing: border-box; }
  html, body { width: 1200px; height: 689px; overflow: hidden; }
  body {
    background: var(--backdrop);
    position: relative;
    font-family: "Arimo", Arial, sans-serif;
  }
  .card {
    position: absolute;
    top: 200px;
    width: 500px;
    height: 286px;
    border-radius: 18px;
    background: var(--navy);
    overflow: hidden;
    box-shadow: 0 18px 40px rgba(0,0,0,0.45);
  }
  .card--front { left: 60px; }
  .card--back { left: 640px; }

  .front-name {
    position: absolute;
    left: 0; right: 0; top: 118px;
    text-align: center;
    font-family: "Cinzel", Georgia, serif;
    font-weight: 600;
    font-size: 34px;
    letter-spacing: 1px;
    color: var(--white);
  }

  .back-panel {
    position: absolute;
    left: 0; top: 0;
    width: 190px; height: 100%;
    background: var(--white);
  }
  .back-mark {
    position: absolute;
    left: 60px; top: 38px;
    width: 210px; height: 210px;
    border-radius: 50%;
    background: var(--white);
    display: flex; align-items: center; justify-content: center;
  }
  .back-mark__name {
    font-family: "Cinzel", Georgia, serif;
    font-weight: 600;
    font-size: 22px;
    line-height: 1.2;
    color: var(--navy);
    text-align: center;
  }

  .contact {
    position: absolute;
    right: 26px; top: 38px;
    text-align: right;
    color: var(--white);
  }
  .contact__name {
    font-family: "Cinzel", Georgia, serif;
    font-weight: 600;
    font-size: 19px;
    letter-spacing: 0.5px;
  }
  .contact__title {
    font-size: 11px;
    color: var(--muted);
    margin-top: 2px;
    margin-bottom: 22px;
  }
  .contact__address { font-size: 12px; line-height: 1.4; margin-bottom: 14px; padding-right: 20px; }
  .contact__list { list-style: none; font-size: 12px; line-height: 1.55; }
  .contact__list li { display: flex; justify-content: flex-end; align-items: center; gap: 8px; }
  .contact__list svg { width: 11px; height: 11px; fill: var(--white); flex: none; }
</style>
</head>
<body>

  <section class="card card--front" aria-label="Card front">
    <div class="front-name">Corvane Capital</div>
  </section>

  <section class="card card--back" aria-label="Card back">
    <div class="back-panel"></div>
    <div class="back-mark">
      <div class="back-mark__name">Corvane<br>Capital</div>
    </div>

    <div class="contact">
      <div class="contact__name">Elias Marlow</div>
      <div class="contact__title">President</div>
      <div class="contact__address">412 Harbor Crest Road<br>Fairhaven, Canada 20815</div>
      <ul class="contact__list">
        <li>555-210-4418
          <svg viewBox="0 0 12 12"><path d="M2.5 1l2 2.2-1 1.3a6 6 0 0 0 4 4l1.3-1 2.2 2-1.3 1.5C5 11 1 7 1 2.3z"/></svg>
        </li>
        <li>555-210-7732
          <svg viewBox="0 0 12 12"><path d="M3 0h6v12H3zM4 1.5v8h4v-8z"/></svg>
        </li>
        <li>info@corvanecapital.com
          <svg viewBox="0 0 12 12"><path d="M0 2h12v8H0zM1 3l5 3.5L11 3v-.2H1z"/></svg>
        </li>
        <li>www.corvanecapital.com
          <svg viewBox="0 0 12 12"><circle cx="6" cy="6" r="5.5"/></svg>
        </li>
      </ul>
    </div>
  </section>

</body>
</html>
```